Bramblewood Card Company Business Cards

We are a trading card store with Glimmorax, sports and other TCG cards, we need a business card design that encompasses a clean cut, modern style with a retro flare. website is bramblewoodcardco.com for reference. Can utilize a comic book era feel or a more modern outdoor feel to utilize the "Pacific Northwest" elements of tress, mountains, etc.

Industry/Entity Type

Trading cards and collectibles

Contact Information for Business Card

business name, email address, phone number, name, owner job title

Font styles to use
Sans Serif

```html
<!DOCTYPE html>
<html lang="en">
<head>
<meta charset="utf-8">
<title>Bramblewood Card Company – Business Cards</title>
<link rel="stylesheet" href="https://fonts.googleapis.com/css2?family=Montserrat:wght@400;500;700&display=swap">
<style>
  :root {
    --backdrop: #d4d7d8;
    --paper: #f7f7f6;
    --ink: #2f3032;
    --ink-soft: #4a4b4d;
    --teal: #1c9dc6;
    --slate: #5d5e60;
    --slate-dark: #3c3d3f;
    --rule: #8c8d8f;
  }
  * { box-sizing: border-box; margin: 0; padding: 0; }
  html, body { width: 1200px; height: 829px; overflow: hidden; }
  body {
    background: var(--backdrop);
    font-family: "Montserrat", sans-serif;
    display: flex;
    align-items: center;
    justify-content: center;
    gap: 40px;
  }
  .card {
    position: relative;
    width: 540px;
    height: 309px;
    overflow: hidden;
    box-shadow: 0 10px 24px rgba(0,0,0,0.18);
  }

  /* Front */
  .card--front { background: var(--paper); color: var(--ink); }
  .holder { position: absolute; left: 34px; top: 56px; }
  .holder__name {
    color: var(--teal);
    font-weight: 700;
    font-size: 22px;
    letter-spacing: 1.5px;
  }
  .holder__title { font-size: 12px; margin-top: 3px; color: var(--ink-soft); }
  .holder__rule { width: 74px; height: 1px; background: var(--rule); margin-top: 10px; }
  .contact { list-style: none; margin-top: 12px; }
  .contact li {
    display: flex; align-items: center; gap: 8px;
    font-size: 12px; line-height: 20px; color: var(--ink);
  }
  .contact svg { width: 10px; height: 10px; fill: var(--teal); flex: none; }
  .divider {
    position: absolute; left: 34px; right: 70px; top: 214px;
    height: 1px; background: var(--rule);
  }
  .mark {
    position: absolute; right: 40px; top: 92px;
    width: 150px; display: flex; align-items: center; gap: 8px;
  }
  .mark__dot { width: 14px; height: 14px; border-radius: 50%; background: var(--teal); flex: none; }
  .mark__name {
    font-weight: 700; font-size: 14px; line-height: 1.2;
    color: var(--slate-dark); text-transform: uppercase; letter-spacing: 0.5px;
  }
  .address {
    position: absolute; right: 34px; bottom: 30px;
    text-align: right; font-size: 12px; line-height: 17px; color: var(--ink);
    font-style: normal;
  }
  .band { position: absolute; left: 0; bottom: 0; width: 540px; height: 14px; display: block; }

  /* Back */
  .card--back { background: var(--slate); display: flex; align-items: center; justify-content: center; }
  .card--back .mark { position: static; width: auto; gap: 12px; }
  .card--back .mark__dot { width: 22px; height: 22px; }
  .card--back .mark__name { color: #f1f1f0; font-size: 20px; letter-spacing: 1px; }
</style>
</head>
<body>

  <section class="card card--front" aria-label="Business card front">
    <div class="holder">
      <h1 class="holder__name">DORIAN HALE</h1>
      <p class="holder__title">CEO/Founder</p>
      <div class="holder__rule"></div>
      <ul class="contact">
        <li>
          <svg viewBox="0 0 10 10"><path d="M2 0.5 L3.6 0.5 L4.2 2.8 L3.1 3.6 Q4 5.8 6.2 6.9 L7 5.8 L9.4 6.4 L9.4 8 Q9.4 9.5 7.8 9.4 Q1 8.6 0.6 2 Q0.5 0.5 2 0.5Z"/></svg>
          (555) 318 2064
        </li>
        <li>
          <svg viewBox="0 0 10 10"><path d="M0 2 L10 2 L10 8.5 L0 8.5Z M0.6 2.4 L5 5.6 L9.4 2.4" stroke="#f7f7f6" stroke-width="0.8"/></svg>
          info@bramblewoodcardco.com
        </li>
        <li>
          <svg viewBox="0 0 10 10"><circle cx="5" cy="5" r="4.6"/><path d="M0.4 5 H9.6 M5 0.4 V9.6" stroke="#f7f7f6" stroke-width="0.7"/></svg>
          www.bramblewoodcardco.com
        </li>
      </ul>
    </div>

    <div class="mark">
      <span class="mark__dot"></span>
      <span class="mark__name">Bramblewood Card Company</span>
    </div>

    <div class="divider"></div>

    <address class="address">
      P.O. Box 7310 Street<br>
      Cedar Vale WA 98012
    </address>

    <svg class="band" viewBox="0 0 540 14" preserveAspectRatio="none" aria-hidden="true">
      <rect x="0" y="0" width="540" height="14" fill="var(--slate-dark)"/>
      <polygon points="0,0 300,0 290,14 0,14" fill="var(--teal)"/>
      <polygon points="300,0 312,0 302,14 290,14" fill="var(--paper)"/>
    </svg>
  </section>

  <section class="card card--back" aria-label="Business card back">
    <div class="mark">
      <span class="mark__dot"></span>
      <span class="mark__name">Bramblewood Card Company</span>
    </div>
  </section>

</body>
</html>
```